Upscale business cards needed for Board of Directors

We need professional business cards created for members of our family business Board of Directors. We would like these relatively simple and straightforward, but also with a unique element to set them apart. Probably stick with neutral and simple colors - white, grey etc. We need space for the traditional elements, including name, title, address, email/phone number. And we will be creating several from this template so it needs to be template that is easy to switch information in and out of.
Business
See description

```html
<!DOCTYPE html>
<html lang="en">
<head>
<meta charset="utf-8">
<title>Harborline Holdings — Business Card</title>
<link rel="stylesheet" href="https://fonts.googleapis.com/css2?family=Roboto:wght@400;700&display=swap">
<style>
  :root {
    --bg: #e8e5df;
    --card: #fbfbfa;
    --sand: #c8bea4;
    --ink: #2a2828;
  }
  * { box-sizing: border-box; margin: 0; padding: 0; }
  html, body { width: 1200px; height: 858px; overflow: hidden; }
  body {
    background: var(--bg);
    font-family: "Roboto", Arial, sans-serif;
    color: var(--ink);
    position: relative;
  }
  .card {
    position: absolute;
    top: 274px;
    width: 540px;
    height: 309px;
    background: var(--card);
    box-shadow: 0 2px 10px rgba(0,0,0,.12);
    overflow: hidden;
  }
  .card--front { left: 40px; }
  .card--back { left: 620px; }

  .swoosh { position: absolute; inset: 0; width: 100%; height: 100%; }

  .brand {
    position: absolute;
    display: flex;
    flex-direction: column;
  }
  .brand-rule {
    display: block;
    height: 4px;
    background: var(--sand);
  }
  .brand-name {
    font-weight: 700;
    color: var(--ink);
    line-height: 1;
    white-space: nowrap;
  }
  .card--front .brand { left: 34px; top: 30px; }
  .card--front .brand-rule { width: 250px; margin-bottom: 10px; }
  .card--front .brand-name { font-size: 26px; }

  .card--back .brand { left: 0; right: 0; top: 124px; align-items: center; }
  .card--back .brand-rule { width: 320px; margin-bottom: 14px; }
  .card--back .brand-name { font-size: 34px; }

  .contact-list {
    position: absolute; right: 22px; top: 112px;
    list-style: none;
    font-size: 15px;
    color: var(--ink);
  }
  .contact-list li {
    display: flex; align-items: center; justify-content: flex-end;
    gap: 10px; height: 30px;
  }
  .contact-icon {
    width: 16px; height: 16px;
    background: var(--sand);
    display: inline-flex; align-items: center; justify-content: center;
  }
  .contact-icon svg { width: 10px; height: 10px; fill: var(--ink); }

  .holder {
    position: absolute; left: 34px; bottom: 22px;
    color: var(--ink);
  }
  .holder-name { font-size: 17px; }
  .holder-title { font-size: 13px; margin-top: 2px; }
</style>
</head>
<body>

<section class="card card--front" aria-label="Business card front">
  <svg class="swoosh" viewBox="0 0 540 309" preserveAspectRatio="none" aria-hidden="true">
    <defs>
      <linearGradient id="sandFill" x1="0" y1="0" x2="1" y2="1">
        <stop offset="0" stop-color="#c3b89c"/>
        <stop offset="1" stop-color="#d9d0b9"/>
      </linearGradient>
    </defs>
    <path d="M0,198 C150,262 300,294 470,309 L0,309 Z" fill="url(#sandFill)"/>
    <path d="M0,176 C140,246 300,282 470,300 C300,276 150,236 0,188 Z" fill="#2a2828"/>
  </svg>

  <div class="brand">
    <span class="brand-rule"></span>
    <h1 class="brand-name">Harborline Holdings</h1>
  </div>

  <ul class="contact-list">
    <li>021-555-0142
      <span class="contact-icon"><svg viewBox="0 0 10 10"><path d="M2 1 L4 1 L4.5 3 L3.4 3.8 C4 5 5 6 6.2 6.6 L7 5.5 L9 6 L9 8 C5 8.5 1.5 5 2 1 Z"/></svg></span>
    </li>
    <li>harborlineholdings@.com
      <span class="contact-icon"><svg viewBox="0 0 10 10"><path d="M1 2.5 H9 V7.5 H1 Z M1.6 3 L5 5.5 L8.4 3 Z" fill-rule="evenodd"/></svg></span>
    </li>
    <li>480 N Linden Ave
      <span class="contact-icon"><svg viewBox="0 0 10 10"><path d="M5 0.8 C3 0.8 2 2.2 2 3.6 C2 5.8 5 9.2 5 9.2 C5 9.2 8 5.8 8 3.6 C8 2.2 7 0.8 5 0.8 Z M5 2.6 A1 1 0 1 0 5 4.6 A1 1 0 1 0 5 2.6 Z" fill-rule="evenodd"/></svg></span>
    </li>
  </ul>

  <div class="holder">
    <p class="holder-name">Evan Porter</p>
    <p class="holder-title">Managing Director</p>
  </div>
</section>

<section class="card card--back" aria-label="Business card back">
  <div class="brand">
    <span class="brand-rule"></span>
    <h2 class="brand-name">Harborline Holdings</h2>
  </div>
</section>

</body>
</html>
```